Business Card Design Can you design a business card design? Looking for something unique and differe

Can you design a business card design? Looking for something unique and different. Can you design a business card design? Looking for something unique and different.Can you design a business card design? Looking for something unique and different.Can you design a business card design? Looking for something unique and different.Can you design a business card design? Looking for something unique and different.Can you design a business card design? Looking for something unique and different.

Industry/Entity Type

Business

Contact Information for Business Card

Can you design a business card design? Looking for something unique and different.

Font styles to use
Serif

```html
<!DOCTYPE html>
<html lang="en">
<head>
<meta charset="utf-8">
<title>Remedia business card</title>
<link href="https://fonts.googleapis.com/css2?family=Varela+Round&family=Open+Sans:ital,wght@0,400;0,600;1,400&display=swap" rel="stylesheet">
<style>
  :root{
    --backdrop:#e3e3e3;
    --card-black:#111112;
    --card-black-soft:#2a2a2c;
    --card-white:#ffffff;
    --brand-purple:#8e739f;
    --band-grey:#8a8a8a;
    --ink:#2b2b2b;
    --ink-soft:#6b6b6b;
  }
  *{box-sizing:border-box;margin:0;padding:0}
  html,body{width:1200px;height:852px;overflow:hidden}
  body{
    background:var(--backdrop);
    font-family:"Open Sans",sans-serif;
    position:relative;
  }
  .card{
    position:absolute;
    width:500px;height:286px;
    border-radius:12px;
    overflow:hidden;
    box-shadow:0 8px 22px rgba(0,0,0,.22);
  }
  /* front */
  .card-front{
    left:70px;top:283px;
    background:linear-gradient(125deg,var(--card-black) 0%,var(--card-black-soft) 45%,var(--card-black) 75%);
    display:flex;align-items:center;justify-content:center;
  }
  .brand{display:flex;flex-direction:column;align-items:center}
  .brand-row{display:flex;align-items:center;gap:14px}
  .brand-square{width:30px;height:30px;background:var(--brand-purple)}
  .brand-name{
    font-family:"Varela Round",sans-serif;
    color:var(--brand-purple);
    font-size:50px;line-height:1;
  }
  .brand-tagline{
    display:flex;align-items:center;gap:8px;
    margin-top:6px;
    font-family:"Varela Round",sans-serif;
    font-size:10px;letter-spacing:4px;
    color:#9a9a9a;
  }
  .brand-tagline::before,.brand-tagline::after{
    content:"";width:46px;height:1px;background:#777;
  }
  /* back */
  .card-back{
    left:630px;top:283px;
    background:var(--card-white);
  }
  .side-band{
    position:absolute;left:0;top:0;bottom:0;width:46px;
    background:var(--brand-purple);
  }
  .side-band::after{
    content:"";position:absolute;right:-8px;top:0;bottom:0;width:8px;
    background:var(--band-grey);
  }
  .back-brand{
    position:absolute;left:96px;top:26px;
    align-items:flex-start;
  }
  .back-brand .brand-name{font-size:38px}
  .back-brand .brand-square{width:24px;height:24px}
  .back-brand .brand-tagline{font-size:8px;letter-spacing:3px;margin-left:38px;color:#888}
  .back-brand .brand-tagline::before,.back-brand .brand-tagline::after{background:#999;width:40px}
  .person{position:absolute;left:84px;top:118px}
  .person-name{
    font-family:"Varela Round",sans-serif;
    color:var(--brand-purple);font-size:17px;
  }
  .person-role{font-size:10px;font-style:italic;color:var(--ink);margin-top:2px}
  .contacts{position:absolute;left:84px;top:176px;list-style:none}
  .contacts li{
    display:flex;align-items:center;gap:10px;
    font-size:12px;color:var(--ink);height:20px;
  }
  .contacts svg{width:12px;height:12px;fill:var(--ink-soft);flex:none}
</style>
</head>
<body>
  <section class="card card-front" aria-label="Card front">
    <div class="brand">
      <div class="brand-row">
        <span class="brand-square"></span>
        <span class="brand-name">Remedia</span>
      </div>
      <div class="brand-tagline">cost management</div>
    </div>
  </section>

  <section class="card card-back" aria-label="Card back">
    <div class="side-band"></div>
    <div class="brand back-brand">
      <div class="brand-row">
        <span class="brand-square"></span>
        <span class="brand-name">Remedia</span>
      </div>
      <div class="brand-tagline">cost management</div>
    </div>

    <div class="person">
      <div class="person-name">Your Long Name</div>
      <div class="person-role">Managing Director</div>
    </div>

    <ul class="contacts">
      <li>
        <svg viewBox="0 0 24 24" aria-hidden="true"><path d="M6.6 10.8a15.1 15.1 0 0 0 6.6 6.6l2.2-2.2c.3-.3.7-.4 1-.2 1.1.4 2.3.6 3.6.6.6 0 1 .4 1 1V20c0 .6-.4 1-1 1C10.6 21 3 13.4 3 4c0-.6.4-1 1-1h3.5c.6 0 1 .4 1 1 0 1.3.2 2.5.6 3.6.1.3 0 .7-.2 1z"/></svg>
        00.00.00.0000
      </li>
      <li>
        <svg viewBox="0 0 24 24" aria-hidden="true"><path d="M2 5h20v14H2zM4 7v.5l8 5 8-5V7zm0 2.8V17h16V9.8l-8 5z"/></svg>
        yourname@yourwebsite.com
      </li>
      <li>
        <svg viewBox="0 0 24 24" aria-hidden="true"><path d="M12 2a10 10 0 1 0 0 20 10 10 0 0 0 0-20zm6.9 6h-3a15 15 0 0 0-1.3-3.9A8 8 0 0 1 18.9 8zM12 4c.8 1.2 1.5 2.5 1.9 4h-3.8c.4-1.5 1.1-2.8 1.9-4zM4.3 14a8 8 0 0 1 0-4h3.4a16 16 0 0 0 0 4zm.8 2h3a15 15 0 0 0 1.3 3.9A8 8 0 0 1 5.1 16zm3-8h-3a8 8 0 0 1 4.3-3.9A15 15 0 0 0 8.1 8zM12 20c-.8-1.2-1.5-2.5-1.9-4h3.8c-.4 1.5-1.1 2.8-1.9 4zm2.3-6H9.7a14 14 0 0 1 0-4h4.6a14 14 0 0 1 0 4zm.3 5.9a15 15 0 0 0 1.3-3.9h3a8 8 0 0 1-4.3 3.9zm1.7-5.9a16 16 0 0 0 0-4h3.4a8 8 0 0 1 0 4z"/></svg>
        www.yourwebsite.com
      </li>
      <li>
        <svg viewBox="0 0 24 24" aria-hidden="true"><path d="M12 2a7 7 0 0 0-7 7c0 5.2 7 13 7 13s7-7.8 7-13a7 7 0 0 0-7-7zm0 9.5a2.5 2.5 0 1 1 0-5 2.5 2.5 0 0 1 0 5z"/></svg>
        Your Commercial or office address with pincode
      </li>
    </ul>
  </section>
</body>
</html>
```